2-Page Flyer for the Information Session about the Quiet Pathfinder Course

This is a flyer to announce/advertise an evening Information Session about the Quiet Pathfinder Course. This Program aims at mindfully rethinking and redesigning work (and life) for people who feel stuck or not entirely satisfied with their work and/or life (please see draft flyer attached for more details). This Program is property of Bright Meadow, a company that uses a combination of Mindfulness, Design, and Entrepreneurship to help people achieve greater happiness (in their work and lives).

Target Market(s)

People who feel stuck or not entirely satisfied with their work and/or life (please see draft flyer attached for more details)

Font styles to use
Serif
Sans Serif

Colors
ffffff
f37122
33a6d7
acd037

Requirements
Must have
• All of what I will say below is suggestive (I’m not a design expert), and I’m open to divert from it, if it makes sense and feels more interesting.
• I thought initially of a 2-page flyer (please see draft flyer attached). The first page could help people grasp the essence of the event quickly (in 1 or 2 minutes), and then, if they are interested/motivated, they would continue reading through page 2, which has more info about the Program in itself.
• Potential Structure
• Page 1
• . About the Information Session on the Quiet Pathfinder Course
• . Visible Date & Time, Contacts, Venue (and other relevant info)
• . About me (the facilitator)
• Page 2
• . About the Quiet Pathfinder Course
• I include a Powerpoint draft of the flyer with the content. The design is rudimentary and precarious from an aesthetics/organization point of view, and this is mainly where I need help (and maybe in other aspects too!).
• On the flyer, I would like to include:
• . A photo of myself (I attach 1 picture).
• . 1 or 2 beautiful-nature photos (cropped or full). One may have to do with looking at the sky, dreaming, and imagining a new work and life (2 photos with sky and clouds attached). The other has to do with walking the transformation journey (the photo with the person walking through the forest path).
• . bright meadow logo or logos (there are two slightly different ones, that can be used for different purposes). For the first page, I would like the bright meadow logo that has "bright meadow" written on the bottom, with the saying "Stillness, Craft and Venture for Bright Meadow" beneath. This is the main logo. For the 2nd page, you can choose the logo that adapts better.
• - Where it says the "the way out is in" it would be great to have a similar font to the one I attach (see file "Font_the_way_out_is_in.png" and Ankecallig-fg.ttf
Nice to have
• In terms of colours, I would not divert much from the logo colours (and of course white and black). I would like the flyer to be quite white. Almost like fairy-tale white: the white horse, the white snow, the white of the stars, the white heaven. White could be the base colour. White means peace, tranquillity, calm contentment, a smile.
• And then use the other colours. The green of the mindfulness. The blue of the sky, the dreams. And the orange of the sun, the energy, the fire, the action. And maybe the black for text.
• Where it says the "the way out is in" it would be great to have a similar font to the one I attach (see file "Font_the_way_out_is_in".
• I would like this flyer to be a piece of art, in every possible way. Simple, beautiful, ease, light, peaceful, calm happy. Just like the Quiet Pathfinder Course and bright meadow Company that I am creating intends to be. The mission of this Program and Company is to be a designer, a painter (a Picasso) of happier and more fulfilling human lives.
• I am very much looking forward to seeing your proposal(s).

```html
<!DOCTYPE html>
<html lang="en">
<head>
<meta charset="utf-8">
<title>Quiet Pathfinder Course – Information Session Flyer</title>
<link rel="stylesheet" href="https://fonts.googleapis.com/css2?family=Ubuntu:wght@700&family=Open+Sans:wght@400;600;700&family=Lato:wght@400;700;900&family=Roboto+Condensed:wght@700&family=Tinos&display=swap">
<style>
:root{
  --orange:#f37122;
  --blue:#33a6d7;
  --green:#acd037;
  --white:#ffffff;
  --ink:#1c1c1c;
  --deep-green:#1f4a1a;
  --grey:#c8c8c8;
  --backdrop:#3b3b3b;
}
*{margin:0;padding:0;box-sizing:border-box}
html,body{width:1200px;height:900px;overflow:hidden;background:var(--backdrop)}
.canvas{position:relative;width:1200px;height:900px}
.page{position:absolute;top:95px;width:504px;height:713px;background:var(--white);overflow:hidden;font-family:"Lato",sans-serif;color:var(--ink)}
.page--front{left:68px}
.page--back{left:610px}
.abs{position:absolute}
.center{left:0;right:0;text-align:center}
.pill{position:absolute;left:50%;transform:translateX(-50%);height:22px;border-radius:11px;color:var(--white);font-family:"Open Sans",sans-serif;font-weight:700;font-size:14px;line-height:22px;text-align:center;white-space:nowrap}
.pill--blue{background:var(--blue)}
.pill--orange{background:var(--orange)}

/* front */
.front__title{top:40px;font-family:"Ubuntu",sans-serif;font-weight:700;font-size:70px;line-height:76px;color:var(--orange);letter-spacing:1px}
.front__subtitle{top:110px;font-family:"Open Sans",sans-serif;font-size:29px;line-height:34px;color:var(--ink)}
.front__date{top:157px;height:35px;background:var(--green);color:var(--white);font-family:"Open Sans",sans-serif;font-weight:600;font-size:19.5px;line-height:35px}
.front__venue{top:201px;font-family:"Open Sans",sans-serif;font-weight:600;font-size:13.5px}
.front__blurb{left:26px;right:26px;text-align:center;font-weight:700;font-size:9.4px;line-height:12px;color:var(--deep-green)}
.front__facilitator{top:415px;font-family:"Open Sans",sans-serif;font-weight:700;font-size:14px}
.front__photo{left:54px;top:443px;width:124px;height:159px}
.front__bio{left:196px;top:456px;width:274px;font-size:8.8px;line-height:11.2px;text-align:justify}
.brand{left:284px;top:614px;display:flex;align-items:center;gap:8px}
.brand__dot{width:30px;height:30px;border-radius:50%;background:var(--blue)}
.brand__name{font-family:"Lato",sans-serif;font-weight:400;font-size:24px;line-height:26px;color:var(--green)}
.front__footer{left:0;top:640px;width:504px;height:73px}
.front__tel{left:31px;top:657px;font-family:"Roboto Condensed",sans-serif;font-weight:700;font-size:19px;color:var(--ink)}
.front__booking{left:31px;top:679px;width:190px;font-size:8.6px;line-height:11px;color:var(--ink)}
.front__web{left:270px;top:697px;font-weight:700;font-size:8.5px;letter-spacing:1.4px;color:var(--ink)}

/* back */
.back__title{top:38px;font-family:"Ubuntu",sans-serif;font-weight:700;font-size:38px;line-height:42px;color:var(--green);letter-spacing:.5px}
.back__subtitle{top:74px;font-family:"Open Sans",sans-serif;font-size:33px;line-height:38px}
.text{font-size:8.6px;line-height:11px;text-align:justify}
.back__intro{left:24px;top:124px;width:456px}
.back__cycle{left:70px;top:198px;width:175px;height:126px}
.back__about{left:248px;top:206px;width:232px}
.back__program{left:24px;top:364px;width:216px}
.ticks{position:absolute;list-style:none}
.ticks li{position:relative;padding-left:18px;font-size:8.6px;line-height:11px;margin-bottom:6px}
.ticks li::before{content:"";position:absolute;left:0;top:1px;width:9px;height:9px;border-radius:50%;background:var(--blue);box-shadow:3px 3px 0 -1px var(--orange)}
.back__gains{left:262px;top:364px;width:220px}
.back__lead{top:483px;font-weight:700;font-size:9px}
.back__why-left{left:28px;top:508px;width:214px}
.back__why-right{left:262px;top:508px;width:216px}
.back__divider{left:258px;top:506px;width:1px;height:56px;background:var(--grey)}
.back__format{left:30px;right:30px;top:587px;text-align:center;font-weight:700;font-size:9px;line-height:12px}
.back__motto{top:630px;height:31px;background:var(--green);font-family:"Tinos",serif;font-size:17px;line-height:31px;color:var(--ink);letter-spacing:.5px}
.back__contact{top:676px;font-weight:700;font-size:7.4px;line-height:10px}
.back__contact--left{left:44px}
.back__contact--right{right:34px;text-align:right}
</style>
</head>
<body>
<div class="canvas">

  <section class="page page--front">
    <h1 class="abs center front__title">QUIET</h1>
    <p class="abs center front__subtitle">Pathfinder Course</p>
    <p class="abs center front__date">Thursday 18th July 2019, from 19:30 to 21:00</p>
    <p class="abs center front__venue">Venue: Lumen Coworking, C/ Almendro 14, Barcelona</p>

    <div class="pill pill--blue" style="top:237px;width:170px">Information Session</div>
    <p class="abs front__blurb" style="top:265px">The purpose of this Information Session is to give you a real insight into the Quiet Pathfinder Course and how it can help you get the most out of your work and life.</p>

    <div class="pill pill--orange" style="top:311px;width:248px">How much and who can come?</div>
    <p class="abs front__blurb" style="top:341px">The purpose of this Information Session is to give you a real insight into the Quiet Pathfinder Course and how it can help you get the most out of your work and life.</p>

    <div class="pill pill--blue" style="top:386px;width:120px">Facilitator</div>
    <p class="abs center front__facilitator">Dr Tomas Varela, Visiting Research Fellow, Harrowgate University</p>

    <svg class="abs front__photo" viewBox="0 0 124 159" role="img" aria-label="Portrait photo of the facilitator">
      <defs>
        <linearGradient id="portraitTone" x1="0" y1="0" x2="0" y2="1">
          <stop offset="0" stop-color="#e6dde0"/>
          <stop offset=".55" stop-color="#c9aea4"/>
          <stop offset="1" stop-color="#4d5867"/>
        </linearGradient>
      </defs>
      <ellipse cx="62" cy="79.5" rx="59.5" ry="77" fill="url(#portraitTone)" stroke="var(--green)" stroke-width="4"/>
    </svg>

    <p class="abs front__bio">Tomas joined Harrowgate University (School of Management) as a Lecturer in Entrepreneurship in 2015. He completed his PhD in Entrepreneurship at Kelburn Business School (University of Kelburn) in 2014. His dissertation received the Marlow Doctoral Dissertation Award from the Society of Enterprise Studies. Tomas began his working career in the semiconductor industry as a production engineer (Solvane), and then in healthcare as a sales engineer (Medrix). After his MBA, he worked as a strategy consultant at Douro Business School. Originally from Portugal, Tomas enjoys designing and launching new ideas, international communities, mindfulness retreats, and musical improvisation.</p>

    <div class="abs brand">
      <span class="brand__dot"></span>
      <span class="brand__name">bright meadow</span>
    </div>

    <svg class="abs front__footer" viewBox="0 0 504 73" aria-hidden="true">
      <path d="M0 0 H222 C240 0 250 10 252 28 L252 45 H504 V73 H0 Z" fill="var(--green)"/>
    </svg>
    <p class="abs front__tel">Tel: +34 611 402 735</p>
    <p class="abs front__booking">Information &amp; Booking: Please contact for more information or to book a place</p>
    <p class="abs front__web">www.brightmeadow.io/tomas</p>
  </section>

  <section class="page page--back">
    <h2 class="abs center back__title">WHAT IS MINDFUL</h2>
    <p class="abs center back__subtitle">Entrepreneurship</p>
    <p class="abs text back__intro">Being mindful means being aware and awake. Entrepreneurship is the creation of a new form of organising. Mindful Entrepreneurship is then the process of creating or redesigning your work and life with awareness, in a way that is reflective of you, of your passions and values, thus conducing to a greater sense of fulfilment and happiness.</p>

    <div class="pill pill--orange" style="top:171px;width:308px">What is Mindful Entrepreneurship</div>

    <svg class="abs back__cycle" viewBox="0 0 175 126" role="img" aria-label="Cycle of four workshops joined by weekly peer support meetings">
      <defs>
        <marker id="arrowHead" viewBox="0 0 6 6" refX="3" refY="3" markerWidth="5" markerHeight="5" orient="auto"><path d="M0 0 L6 3 L0 6 Z" fill="var(--grey)"/></marker>
      </defs>
      <g font-family="Lato,sans-serif" font-size="4.2" text-anchor="middle" fill="var(--white)">
        <circle cx="86" cy="28" r="25" fill="var(--green)"/>
        <text x="86" y="23">Workshop 1</text><text x="86" y="29">-INSIGHT-</text><text x="86" y="35">(5 hours)</text>
        <circle cx="130" cy="64" r="25" fill="var(--blue)"/>
        <text x="130" y="59">Workshop 2</text><text x="130" y="65">-DESIGN-</text><text x="130" y="71">(5 hours)</text>
        <circle cx="86" cy="100" r="25" fill="var(--orange)"/>
        <text x="86" y="95">Workshop 3</text><text x="86" y="101">-EXECUTE-</text><text x="86" y="107">(5 hours)</text>
        <circle cx="42" cy="64" r="25" fill="var(--grey)"/>
        <text x="42" y="59">Workshop 4</text><text x="42" y="65">-PRESENT-</text><text x="42" y="71">(5 hours)</text>
      </g>
      <g stroke="var(--grey)" stroke-width="2" fill="none" marker-end="url(#arrowHead)">
        <path d="M112 32 L122 40"/>
        <path d="M122 92 L112 99"/>
        <path d="M60 99 L50 92"/>
        <path d="M50 36 L60 29"/>
      </g>
      <g font-family="Lato,sans-serif" font-size="4" fill="#555">
        <text x="118" y="24">Weekly Peer Support</text><text x="118" y="29">(WPS) meetings</text>
        <text x="120" y="104">WPS meetings</text>
        <text x="22" y="104">WPS meetings</text>
        <text x="18" y="28">WPS meetings</text>
      </g>
    </svg>

    <p class="abs text back__about">The Quiet Pathfinder Course is a 4-month long transformative journey for people who feel stuck or not entirely satisfied with their work and/or life. It will be of benefit for everyone, at any stage. The Program consists of a series of four 5-hour workshops, one per month, complemented by 2-hour weekly peer support meetings. It combines mindfulness techniques, design thinking methodology and entrepreneurship frameworks to achieve the desired</p>

    <div class="pill pill--blue" style="top:331px;width:174px">The Program</div>
    <p class="abs text back__program">Many people are not entirely satisfied with their work, but they don't know what to do about it. The Quiet Pathfinder Course offers an opportunity, a safe place, a collective journey to help you reflect, design, and (very likely) do something about it. By the end of the Program, you should have:</p>
    <ul class="ticks back__gains">
      <li>Increased awareness, clarity and confidence</li>
      <li>A deeper insight on what makes you happier and what you want</li>
      <li>A clear design integrating your intended work and life Initiated the execution of this design.</li>
    </ul>

    <div class="pill pill--orange" style="top:446px;width:112px">Why</div>
    <p class="abs center back__lead">This Program differs from existing entrepreneurial programs in many ways:</p>
    <ul class="ticks back__why-left">
      <li>It starts upstream with mindfulness and self analysis to look deeply into yourself</li>
      <li>Design and execution decisions are rooted on happiness rather than (only) financials</li>
    </ul>
    <span class="abs back__divider"></span>
    <ul class="ticks back__why-right">
      <li>The process is holistic and inclusive, aiming at designing an integrated work and life, and on building synergies between your different parts.</li>
    </ul>
    <p class="abs back__format">The Program format includes lectures, individual work, group sharing, guided activities, experiential exercises, video, audio, handouts and other resources.</p>

    <p class="abs center back__motto">THE WAY OUT IS IN</p>
    <p class="abs back__contact back__contact--left">Date: Thursday 23th, from 19:30 to 21:00<br>Venue: Lumen Coworking, C/ Almendro 14, Barcelona</p>
    <p class="abs back__contact back__contact--right">Email: info@brightmeadow.io<br>Tel: +34 611 402 735 (video call and messaging)</p>
  </section>

</div>
</body>
</html>
```